Business Card for Vorla Parts Wholesale supplier

Hi There! I need a new business card for our company. We are specialized in selling Vorla parts, mostly we sell new LCD screens for Zelnar and Drelks. I would like to see that back in the design.

You can find the colors and logo's on our website: www.hartuvo.nl

Industry/Entity Type

Business

Contact Information for Business Card

My Details:
Tobias Lindqvist

Phone: 0031687203316
E-mail: Tobias@hartuvo.nl

Slogan: "Built For Every Repair"

Font styles to use
Sans Serif

Colors

Designer to choose colors to be used in the design.

Requirements
Must have
• A Black backside with the Hartuvo logo on it. The front side should be clean with only my contact details.
• But I'm also open for something really different or awesome!
Nice to have
• Remember that we are in the parts & repairing industry, So i'll be handing those business cards mainly to repair companies. Maybe you can do something with that thought :)

```html
<!DOCTYPE html>
<html lang="en">
<head>
<meta charset="utf-8">
<title>Hartuvo – Business Card</title>
<link rel="stylesheet" href="https://fonts.googleapis.com/css2?family=Exo+2:wght@600&family=Open+Sans:wght@400;600;700&display=swap">
<style>
  :root {
    --bg: #232323;
    --orange: #f27a2c;
    --orange-deep: #e2631a;
    --black: #0c0c0c;
    --white: #ffffff;
  }
  * { margin: 0; padding: 0; box-sizing: border-box; }
  html, body { width: 1200px; height: 950px; overflow: hidden; background: var(--bg); }
  .canvas { position: relative; width: 1200px; height: 950px; }
  .card {
    position: absolute; left: 250px; width: 700px; height: 400px;
    border-radius: 4px; overflow: hidden;
  }
  .card--front {
    top: 55px;
    background: linear-gradient(120deg, var(--orange) 0%, var(--orange-deep) 100%);
    color: var(--white);
    font-family: "Open Sans", sans-serif;
  }
  .card--back {
    top: 495px;
    background: var(--black);
    display: flex; align-items: center; justify-content: center; gap: 18px;
  }
  .brand {
    font-family: "Exo 2", sans-serif; font-weight: 600;
    color: var(--white); letter-spacing: 1px; line-height: 1;
  }
  .card--front .brand { position: absolute; left: 52px; top: 58px; font-size: 64px; }
  .card--back .brand { font-size: 72px; }
  .brand-dot { width: 46px; height: 46px; border-radius: 50%; background: var(--orange); }
  .details { position: absolute; left: 56px; top: 165px; }
  .details__name { font-size: 25px; font-weight: 700; margin-bottom: 14px; }
  .details__line { display: flex; align-items: center; gap: 10px; font-size: 16px; margin-bottom: 7px; }
  .details__line svg { width: 16px; height: 16px; fill: var(--white); flex: none; }
  .details__slogan { font-size: 17px; font-weight: 700; margin-top: 12px; }
</style>
</head>
<body>
<main class="canvas">
  <section class="card card--front">
    <div class="brand">hartuvo</div>
    <div class="details">
      <p class="details__name">Tobias Lindqvist</p>
      <p class="details__line">
        <svg viewBox="0 0 16 16" aria-hidden="true"><path d="M3 1h3l1.5 4-2 1.3a9 9 0 0 0 4.2 4.2L11 8.5l4 1.5v3a2 2 0 0 1-2 2A12 12 0 0 1 1 3a2 2 0 0 1 2-2z"/></svg>
        0031687203316
      </p>
      <p class="details__line">
        <svg viewBox="0 0 16 16" aria-hidden="true"><path d="M1 3h14v10H1z M2 4.2v.4l6 4 6-4v-.4z" fill-rule="evenodd"/></svg>
        Tobias@hartuvo.nl
      </p>
      <p class="details__line">
        <svg viewBox="0 0 16 16" aria-hidden="true"><circle cx="8" cy="8" r="7"/></svg>
        www.hartuvo.nl
      </p>
      <p class="details__slogan">Built For Every Repair</p>
    </div>
  </section>
  <section class="card card--back">
    <span class="brand-dot"></span>
    <span class="brand">hartuvo</span>
  </section>
</main>
</body>
</html>
```